Business Card Design for company

We want new business cards. We'd like something different-- yet still highly professional. Our tagline is Providing leadership, delivering success. Stock photos are ok, as long as they are relevant and look upscale.

Target Market(s)

Architecture/Business Management Consulting/Engineering Consulting

Contact Information for Business Card

dark gray background with pops of blue might be good, but you tell me. You're the designers. Rounded corners might be nice, but again, you tell me.

Font styles to use
Serif
Sans Serif

Colors
3276b5
5c5c5c
9d9d9d
fbfbfb

Requirements
Nice to have
• Something different, but still very professional.

```html
<!DOCTYPE html>
<html lang="en">
<head>
<meta charset="utf-8">
<title>Ostrava Partners — Business Cards</title>
<link rel="stylesheet" href="https://fonts.googleapis.com/css2?family=Mulish:ital,wght@0,400;0,600;0,800;1,400&display=swap">
<style>
  :root {
    --blue: #3276b5;
    --charcoal: #5c5c5c;
    --gray: #9d9d9d;
    --paper: #fbfbfb;
    --backdrop: #8c9196;
  }
  html, body {
    margin: 0;
    width: 1154px;
    height: 1200px;
    overflow: hidden;
    background: var(--backdrop);
    font-family: "Mulish", sans-serif;
  }
  .stage {
    position: relative;
    width: 1154px;
    height: 1200px;
  }
  .card {
    position: absolute;
    top: 180px;
    width: 480px;
    height: 840px;
    background: var(--paper);
    border-radius: 26px;
    overflow: hidden;
    box-shadow: 0 8px 22px rgba(0,0,0,0.25);
  }
  .card--front { left: 70px; }
  .card--back { left: 604px; }

  /* Front */
  .front-block {
    position: absolute;
    left: 133px;
    top: 0;
    width: 214px;
    height: 360px;
    background: var(--blue);
  }
  .front-name {
    position: absolute;
    left: 0;
    right: 0;
    top: 388px;
    text-align: center;
    color: var(--charcoal);
    font-weight: 800;
    font-size: 34px;
    letter-spacing: 1px;
    line-height: 1.15;
    text-transform: uppercase;
  }
  .tagline {
    position: absolute;
    left: 0;
    right: 0;
    bottom: 62px;
    text-align: center;
    color: var(--charcoal);
    font-weight: 800;
    font-size: 23px;
    line-height: 1.45;
    text-transform: uppercase;
    letter-spacing: 0.5px;
  }

  /* Back */
  .back-stripe {
    position: absolute;
    left: 0;
    top: 0;
    width: 62px;
    height: 100%;
    background: var(--blue);
  }
  .back-brand {
    position: absolute;
    right: 34px;
    top: 38px;
    display: flex;
    align-items: center;
    gap: 10px;
    color: var(--charcoal);
    font-weight: 800;
    font-size: 20px;
    letter-spacing: 1px;
    text-transform: uppercase;
  }
  .back-brand .mark {
    width: 14px;
    height: 14px;
    background: var(--blue);
  }
  .contact {
    position: absolute;
    left: 86px;
    right: 28px;
    bottom: 36px;
    color: var(--charcoal);
  }
  .contact-name {
    margin: 0;
    font-weight: 800;
    font-size: 30px;
    letter-spacing: 1px;
    text-transform: uppercase;
    white-space: nowrap;
  }
  .contact-title {
    margin: 0 0 16px;
    font-style: italic;
    font-size: 22px;
  }
  .contact p {
    margin: 0;
    font-size: 20px;
    line-height: 1.45;
  }
  .contact .dot { color: var(--blue); padding: 0 6px; }
  .contact .group { margin-bottom: 12px; }
</style>
</head>
<body>
  <main class="stage">
    <section class="card card--front" aria-label="Card front">
      <div class="front-block"></div>
      <div class="front-name">Ostrava<br>Partners</div>
      <div class="tagline">Offering direction<br>achieving results</div>
    </section>

    <section class="card card--back" aria-label="Card back">
      <div class="back-stripe"></div>
      <div class="back-brand"><span class="mark"></span>Ostrava Partners</div>
      <div class="contact">
        <h1 class="contact-name">Daniel R. Whitmore</h1>
        <p class="contact-title">President</p>
        <div class="group">
          <p>4180 Cedar Point Lane</p>
          <p>Marlow Bay<span class="dot">•</span>Florida<span class="dot">•</span>32100</p>
        </div>
        <div class="group">
          <p>(555) 014-2276</p>
          <p>info@ostravapartners.com</p>
        </div>
        <p>www.ostravapartners.com</p>
      </div>
    </section>
  </main>
</body>
</html>
```